Design the Business card for NetVaultic

Business card required for a professional Cyber Security business.
Company Logo and Icon has already been provided however I would like other options for the logo and icon to compare to. Alternatively, please refine/enhance the image of the logo.icon I have already provided.

If you are going to use the provided logo and icon, I was thinking that the company raised Logo on White background would serve well on the front of the card. See attached. AND, a large company raised stand-alone icon to appear on black background on the back of the card with tagline 'Cyber Risk Management, Governance and Consulting' or 'Cyber Security for your Business' See attached.
Alternatively, provide your own design for the logo and icon.

Target Market(s)

Enterprise, Government, Financial.

Contact Information for Business Card

Tavin Orloweth
Founder and CEO

Email Address
Mobile Number
Website URL
LinkedIn URL

Logo Text

NetVaultic - see attached example of logo

Font styles to use
Other font styles liked:
• Berlin Sans FB

Requirements
Must have
• Clean large and bold icon on the back with tagline.
• Horizontal alignment,
Nice to have
• Round edges.
• Raised Logo/Icon
Should not have
• An unprofessional look and feel.

```html
<!DOCTYPE html>
<html lang="en">
<head>
<meta charset="utf-8">
<title>NetVaultic Business Card</title>
<link rel="stylesheet" href="https://fonts.googleapis.com/css2?family=Roboto:wght@400&family=Roboto+Condensed:wght@500;700&family=Cabin:wght@500;600;700&display=swap">
<style>
  :root {
    --backdrop: #7a5c44;
    --card-white: #f6f6f6;
    --card-dark: #1b1d20;
    --brand-blue: #0b6fc2;
    --mark-blue: #4a72c8;
    --brand-yellow: #f2b705;
    --text-grey: #555a5f;
    --rule-grey: #8c8c8c;
  }
  * { margin: 0; padding: 0; box-sizing: border-box; }
  html, body { width: 1200px; height: 960px; overflow: hidden; }
  body { background: var(--backdrop); position: relative; }

  .card {
    position: absolute;
    width: 600px;
    height: 343px;
    box-shadow: 0 4px 10px rgba(0,0,0,0.35);
  }
  .card-front { left: 314px; top: 113px; background: var(--card-white); }
  .card-back  { left: 311px; top: 472px; background: var(--card-dark); }

  .brand-lockup {
    position: absolute;
    right: 38px;
    top: 42px;
    display: flex;
    align-items: center;
    gap: 12px;
  }
  .brand-dot {
    width: 58px; height: 58px; border-radius: 50%;
    background: var(--mark-blue);
  }
  .brand-name {
    font-family: "Cabin", sans-serif;
    font-weight: 700;
    font-size: 42px;
    color: var(--brand-blue);
    letter-spacing: 0.2px;
  }

  .holder { position: absolute; left: 39px; top: 168px; }
  .holder-name {
    font-family: "Roboto Condensed", sans-serif;
    font-weight: 700;
    font-size: 23px;
    color: var(--brand-blue);
    text-transform: uppercase;
    line-height: 1.1;
  }
  .holder-title {
    font-family: "Roboto Condensed", sans-serif;
    font-weight: 500;
    font-size: 16px;
    color: var(--brand-yellow);
    text-transform: uppercase;
    margin-top: 1px;
  }
  .divider {
    position: absolute; left: 39px; top: 220px;
    width: 525px; height: 1px; background: var(--rule-grey);
  }

  .contact-list { position: absolute; left: 37px; top: 235px; list-style: none; }
  .contact-item {
    display: flex; align-items: center; gap: 8px;
    height: 19.5px;
    font-family: "Roboto", sans-serif;
    font-size: 14.5px;
    color: var(--text-grey);
  }
  .contact-icon { width: 14px; height: 14px; flex: none; }

  .back-mark {
    position: absolute; left: 50%; top: 62px;
    transform: translateX(-50%);
    width: 150px; height: 150px; border-radius: 50%;
    background: var(--mark-blue);
    box-shadow: 0 0 14px rgba(74,114,200,0.5);
  }
  .back-name {
    position: absolute; left: 0; right: 0; top: 222px;
    text-align: center;
    font-family: "Cabin", sans-serif;
    font-weight: 700;
    font-size: 26px;
    color: var(--mark-blue);
  }
  .tagline {
    position: absolute; left: 0; right: 0; top: 276px;
    text-align: center;
    font-family: "Cabin", sans-serif;
    font-weight: 500;
    font-size: 18.5px;
  }
  .tagline-lead { color: var(--mark-blue); }
  .tagline-rest { color: var(--brand-yellow); }
</style>
</head>
<body>
  <section class="card card-front">
    <div class="brand-lockup">
      <span class="brand-dot"></span>
      <span class="brand-name">NetVaultic</span>
    </div>

    <div class="holder">
      <p class="holder-name">Tavin Orloweth</p>
      <p class="holder-title">Founder &amp; CEO</p>
    </div>
    <div class="divider"></div>

    <ul class="contact-list">
      <li class="contact-item">
        <svg class="contact-icon" viewBox="0 0 14 14"><rect x="3.5" y="0.5" width="7" height="13" rx="1.2" fill="#0b6fc2"/><rect x="4.8" y="2" width="4.4" height="8.5" fill="#f6f6f6"/></svg>
        555 014 2738
      </li>
      <li class="contact-item">
        <svg class="contact-icon" viewBox="0 0 14 14"><rect x="1" y="3" width="12" height="8.5" fill="#0b6fc2"/><path d="M1.5 3.5 L7 8 L12.5 3.5" stroke="#f6f6f6" stroke-width="1.2" fill="none"/></svg>
        tavin@netvaultic.com
      </li>
      <li class="contact-item">
        <svg class="contact-icon" viewBox="0 0 14 14"><circle cx="7" cy="7" r="6.2" fill="#0b6fc2"/><path d="M1 7 H13 M7 1 C4 4 4 10 7 13 M7 1 C10 4 10 10 7 13" stroke="#f6f6f6" stroke-width="0.9" fill="none"/></svg>
        www.netvaultic.com
      </li>
      <li class="contact-item">
        <svg class="contact-icon" viewBox="0 0 14 14"><circle cx="7" cy="7" r="6.2" fill="#0b6fc2"/></svg>
        netvaultic
      </li>
    </ul>
  </section>

  <section class="card card-back">
    <div class="back-mark"></div>
    <p class="back-name">NetVaultic</p>
    <p class="tagline"><span class="tagline-lead">Cyber Risk Management,</span> <span class="tagline-rest">Governance &amp; Consulting</span></p>
  </section>
</body>
</html>
```